Business card design for my company.
I would like the card's background colour to be black. You can also see our web site to get an idea of our brand. https://www.tmwhomecrafting.com.au/
- Name
- Email

```html
<!DOCTYPE html>
<html lang="en">
<head>
<meta charset="utf-8">
<title>TMW Home Crafting – Business Card</title>
<link href="https://fonts.googleapis.com/css2?family=Poppins:wght@400;500;600&display=swap" rel="stylesheet">
<style>
  :root {
    --page: #2a2a2a;
    --card: #161616;
    --green: #0f9a47;
    --white: #f2f2f2;
    --muted: #d8d8d8;
  }
  * { box-sizing: border-box; margin: 0; padding: 0; }
  html, body { width: 1200px; height: 875px; overflow: hidden; }
  body {
    background: var(--page);
    font-family: "Poppins", sans-serif;
    display: flex;
    align-items: center;
    justify-content: center;
    gap: 30px;
  }
  .card {
    position: relative;
    width: 555px;
    height: 318px;
    background: var(--card);
    border-radius: 18px;
    overflow: hidden;
  }
  /* front */
  .card--front { border-bottom: 5px solid var(--green); }
  .card--front .brand {
    position: absolute; inset: 0;
    display: flex; align-items: center; justify-content: center; gap: 14px;
  }
  .brand__mark { width: 22px; height: 22px; background: var(--green); }
  .brand__name {
    color: var(--white);
    font-weight: 600;
    font-size: 32px;
    letter-spacing: 3px;
    text-transform: uppercase;
  }
  /* back */
  .card--back .brand {
    position: absolute; left: 30px; top: 112px; width: 210px;
    display: flex; align-items: center; gap: 10px;
  }
  .card--back .brand__mark { width: 14px; height: 14px; flex: none; }
  .card--back .brand__name { font-size: 18px; letter-spacing: 2px; line-height: 1.2; }
  .divider {
    position: absolute; left: 262px; top: 62px;
    width: 1px; height: 120px; background: var(--green);
  }
  .contact { position: absolute; left: 290px; top: 56px; }
  .contact__name { color: var(--green); font-weight: 600; font-size: 22px; line-height: 1.1; }
  .contact__role { color: var(--muted); font-size: 12px; margin-bottom: 16px; }
  .contact__list { list-style: none; }
  .contact__item {
    display: flex; align-items: center; gap: 9px;
    color: var(--muted); font-size: 11.5px; line-height: 1.75;
  }
  .contact__item svg { width: 11px; height: 11px; fill: var(--green); flex: none; }
  .address {
    position: absolute; left: 0; right: 0; bottom: 50px;
    text-align: center; color: var(--green); font-size: 13px; font-weight: 500;
  }
  .band {
    position: absolute; left: 0; right: 0; bottom: 0;
    height: 38px; background: var(--green);
  }
</style>
</head>
<body>
  <section class="card card--front">
    <div class="brand">
      <span class="brand__mark"></span>
      <span class="brand__name">TMW Home Crafting</span>
    </div>
  </section>

  <section class="card card--back">
    <div class="brand">
      <span class="brand__mark"></span>
      <span class="brand__name">TMW Home Crafting</span>
    </div>
    <div class="divider"></div>
    <div class="contact">
      <p class="contact__name">Daniel Hart</p>
      <p class="contact__role">CEO &amp; Founder</p>
      <ul class="contact__list">
        <li class="contact__item">
          <svg viewBox="0 0 24 24"><path d="M6.6 10.8a15.1 15.1 0 0 0 6.6 6.6l2.2-2.2a1 1 0 0 1 1-.25 11.4 11.4 0 0 0 3.6.57 1 1 0 0 1 1 1V20a1 1 0 0 1-1 1A17 17 0 0 1 3 4a1 1 0 0 1 1-1h3.5a1 1 0 0 1 1 1c0 1.25.2 2.45.57 3.57a1 1 0 0 1-.25 1z"/></svg>
          0400 123 456
        </li>
        <li class="contact__item">
          <svg viewBox="0 0 24 24"><path d="M2 5h20v14H2zm2 2v.5l8 5 8-5V7z"/></svg>
          info@tmwhomecrafting.com.au
        </li>
        <li class="contact__item">
          <svg viewBox="0 0 24 24"><circle cx="12" cy="12" r="10"/></svg>
          www.tmwhomecrafting.com.au
        </li>
      </ul>
    </div>
    <p class="address">Greenridge, Westhaven, WH, Northland, Eastmoor</p>
    <div class="band"></div>
  </section>
</body>
</html>
```